Designing a brochures for an educational counseling service provider

We would like a 4 sided design on a 11x8.5 paper, half folded. I have including a sample design we did to give you an idea of what we envision but we welcome creativity to make beautiful looking flyers. Text for the flier is included as well as our logo.
- The most important thing is capturing our audience/market. We will be handing these flies to schools, organizations and individual clients.

www.pvrlearningadvisors.example

Target Market(s)

We are targeting international students wanting to study in the U.S and Canada.

Industry/Entity Type

Education

Requirements
Must have
• - Clean and clear
• - Our logo should visible and well placed.
• - Could you the pictures of students, libraries and school buildings or you could use the pictures we already have.
Nice to have
• We would like this to match business cards.

```html
<!DOCTYPE html>
<html lang="en">
<head>
<meta charset="utf-8">
<title>PVR Learning Advisors – Brochure</title>
<link rel="stylesheet" href="https://fonts.googleapis.com/css2?family=Open+Sans:wght@600;700;800&family=Raleway:wght@400;500;600;700&display=swap">
<style>
  :root {
    --navy: #27307f;
    --blue: #2f5fb3;
    --green: #6cc04a;
    --green-light: #8fd14f;
    --ink: #2b2b2b;
    --paper: #ffffff;
    --backdrop: #e9e7e3;
    --photo-sport-a: #d9c7b4;
    --photo-sport-b: #8f9c7a;
    --photo-cover-a: #6f9a55;
    --photo-cover-b: #c9b9a8;
  }
  * { box-sizing: border-box; margin: 0; padding: 0; }
  html, body { width: 1200px; height: 900px; overflow: hidden; }
  body { background: var(--backdrop); font-family: "Raleway", sans-serif; color: var(--ink); position: relative; }

  .spread { position: absolute; left: 70px; top: 40px; width: 1060px; height: 820px; display: flex; box-shadow: 0 8px 24px rgba(0,0,0,.18); }
  .panel { position: relative; width: 530px; height: 820px; background: var(--paper); overflow: hidden; }
  .panel--back { border-right: 1px solid #ddd; }

  /* back panel */
  .services-text { padding: 24px 38px 0 38px; }
  .section-label { display: inline-block; background: var(--green); color: #fff; font-family: "Open Sans", sans-serif; font-weight: 700; font-size: 13px; padding: 2px 40px 2px 8px; margin-bottom: 3px; }
  .services-text p { font-size: 13px; line-height: 1.3; margin-bottom: 7px; }
  .photo-students-sport { position: absolute; left: 0; top: 405px; width: 530px; height: 180px; background: linear-gradient(160deg, var(--photo-sport-a), var(--photo-sport-b)); }

  .back-footer { position: absolute; left: 0; top: 585px; width: 530px; height: 195px; display: flex; align-items: center; padding: 0 28px; }
  .brand { display: flex; align-items: center; gap: 10px; }
  .brand-dot { width: 34px; height: 34px; border-radius: 50%; background: var(--green); flex: none; }
  .brand-name { font-family: "Raleway", sans-serif; font-weight: 700; font-size: 21px; color: var(--navy); line-height: 1.05; }
  .back-footer .brand { width: 220px; flex: none; }
  .contact { border-left: 1px solid var(--green); padding-left: 12px; font-size: 11px; line-height: 1.4; }
  .contact-title { color: var(--green); font-family: "Open Sans", sans-serif; font-weight: 700; font-size: 12px; }
  .contact-role { font-family: "Open Sans", sans-serif; font-weight: 700; font-size: 12px; margin-bottom: 3px; }
  .bottom-band { position: absolute; left: 0; bottom: 0; width: 530px; height: 40px; background: linear-gradient(90deg, var(--navy), var(--blue)); }

  /* cover panel */
  .photo-students-group { position: absolute; left: 0; top: 100px; width: 530px; height: 460px; background: linear-gradient(170deg, var(--photo-cover-a), var(--photo-cover-b)); }
  .cover-curve { position: absolute; left: 0; top: 0; }
  .cover-brand { position: absolute; right: 36px; top: 58px; }
  .tagline { position: absolute; left: 0; top: 520px; width: 530px; height: 80px; background: var(--navy); color: #fff; font-family: "Open Sans", sans-serif; font-weight: 700; font-size: 17px; text-align: center; padding: 14px 30px; line-height: 1.3; }
  .service-band { position: absolute; left: 0; top: 600px; width: 530px; height: 170px; background: linear-gradient(90deg, var(--green), var(--green-light)); display: flex; justify-content: space-around; align-items: center; padding: 0 10px; border-bottom: 4px solid #fff; }
  .service { display: flex; flex-direction: column; align-items: center; gap: 10px; color: #fff; font-family: "Open Sans", sans-serif; font-weight: 700; font-size: 11.5px; }
  .service-icon { width: 58px; height: 58px; border: 2px solid #fff; border-radius: 50%; display: flex; align-items: center; justify-content: center; }
  .panel--cover .bottom-band { height: 50px; }
</style>
</head>
<body>
<main class="spread">
  <section class="panel panel--back">
    <div class="services-text">
      <span class="section-label">Transfer students</span>
      <p>Need to find a school an alternative school that is a better match for you? We work with students and families to transfer from one school to another.</p>
      <span class="section-label">Boarding schools</span>
      <p>Funding the education for your children in some of the world’s top schools can be very expensive as tuition and fees increase at an average of 4% every year. We work with you to determine the budget for your family, applying to scholarship available and guide you through the financial aid process.</p>
      <p>Over 70% of our clients have been awarded scholarships or Financial Aid, making your education goals attainable an affordable and your children education possible.</p>
      <p>Include at the bottom of last page “Our consultants are members of CEA, the leading association for educational consultants in North America.”</p>
    </div>
    <div class="photo-students-sport" role="img" aria-label="Photo of smiling students in sports jerseys on a field"></div>
    <div class="back-footer">
      <div class="brand">
        <span class="brand-dot"></span>
        <span class="brand-name">PVR Learning Advisors</span>
      </div>
      <div class="contact">
        <div class="contact-title">CONTACT US</div>
        <div class="contact-role">Executive Director &amp; Independent<br>Educational Consultant</div>
        <div>PVR Learning Advisors, LLC</div>
        <div>418 Orchard Lane, Suite 210, Millbrook, TX 75000</div>
        <div>Phone: 555-010-4821</div>
        <div>Email: info@pvrlearningadvisors.example</div>
        <div>www.pvrlearningadvisors.example</div>
      </div>
    </div>
    <div class="bottom-band"></div>
  </section>

  <section class="panel panel--cover">
    <div class="photo-students-group" role="img" aria-label="Photo of a group of smiling students holding notebooks outdoors"></div>
    <svg class="cover-curve" width="530" height="560" viewBox="0 0 530 560" aria-hidden="true">
      <path d="M0 0 H530 V430 Q470 170 0 120 Z" fill="#fff"/>
      <path d="M120 118 Q480 150 530 440" fill="none" stroke="#27307f" stroke-width="7"/>
    </svg>
    <div class="brand cover-brand">
      <span class="brand-dot"></span>
      <span class="brand-name">PVR Learning Advisors</span>
    </div>
    <div class="tagline">A full - service international educational consulting group serving students and families across the globe</div>
    <div class="service-band">
      <div class="service">
        <span class="service-icon">
          <svg width="32" height="32" viewBox="0 0 32 32" fill="none" stroke="#fff" stroke-width="2"><path d="M4 12 L16 5 L28 12 Z"/><path d="M8 14 V24 M13 14 V24 M19 14 V24 M24 14 V24 M4 27 H28"/></svg>
        </span>Boarding Schools
      </div>
      <div class="service">
        <span class="service-icon">
          <svg width="32" height="32" viewBox="0 0 32 32" fill="none" stroke="#fff" stroke-width="2"><path d="M8 4 H20 L25 9 V28 H8 Z"/><path d="M12 13 H21 M12 18 H21 M12 23 H17"/></svg>
        </span>College Admission
      </div>
      <div class="service">
        <span class="service-icon">
          <svg width="32" height="32" viewBox="0 0 32 32" fill="none" stroke="#fff" stroke-width="2"><circle cx="11" cy="10" r="3.5"/><circle cx="21" cy="10" r="3.5"/><path d="M5 22 Q11 15 17 22 M15 22 Q21 15 27 22 M4 25 H28"/></svg>
        </span>Transfer Students
      </div>
      <div class="service">
        <span class="service-icon">
          <svg width="32" height="32" viewBox="0 0 32 32" fill="none" stroke="#fff" stroke-width="2"><path d="M2 12 L16 6 L30 12 L16 18 Z"/><path d="M8 15 V22 Q16 27 24 22 V15 M28 13 V21"/></svg>
        </span>Graduate Students
      </div>
    </div>
    <div class="bottom-band"></div>
  </section>
</main>
</body>
</html>
```